Harrowmere Freight, Project

Company Profile
Harrowmere Freight Sdn Bhd is a well established and experienced freight forwarder in Kuala Lumpur, Malaysia. We specialize in air and sea forwarding, Custom Brokerage and regulatory compliance services, inland transportation,
overseas freighting and warehousing and distribution management. With our dedicated qualified and experienced professionals, we are fully committed to serving our clients.

Our Mission
Based on the motto “Quick, Reliable and Polite”, Harrowmere Freight is dedicated to upholding the following three points corporate philosophy:
1. Adhering to the principle that “the customer always comes first”.
2. Contributing to the development of the local community.
3. Making it our duty to be responsible and sincere.

Our Edge
• One-Stop Logistics Solutions
• Extensive Network Throughout Malaysia
• Highly Qualified and Experienced Pool of Professionals
• Comprehensive IT Solutions
• Innovative and Customer-focused Solutions
• Flexible and Consistent in Managing Exceptions
• Total Supply Chain Visibility

Target Market(s)

We sell the logistics services to all the industry in Malaysia. (ONE Stop Logistics Solutions)

Industry/Entity Type

Logistic

Contact Information for Business Card

I want the back of the card to be white with the logo and slogan. i would like to see the logo on the front with the general info.

Requirements
Must have
• Name, Title, Office, Cell, Fax, Email, Address, Website
Nice to have
• Modern Design Business Card

```html
<!DOCTYPE html>
<html lang="en">
<head>
<meta charset="utf-8">
<title>Harrowmere Freight — Stationery Set</title>
<link href="https://fonts.googleapis.com/css2?family=Open+Sans:wght@400;600;700&family=Arimo:wght@400&display=swap" rel="stylesheet">
<style>
  :root{
    --bg:#e8ebeb;
    --paper:#ffffff;
    --blue:#26a6e0;
    --blue-deep:#0b63b0;
    --ink:#3d3d3d;
    --ink-soft:#6b6b6b;
    --shadow:0 6px 18px rgba(0,0,0,.14);
  }
  *{box-sizing:border-box;margin:0;padding:0}
  html,body{width:1200px;height:900px;overflow:hidden}
  body{background:var(--bg);font-family:"Open Sans",Arial,sans-serif;color:var(--ink);position:relative}

  .brand{font-family:"Open Sans",Arial,sans-serif;font-weight:700;color:var(--blue);display:flex;align-items:center;gap:6px;white-space:nowrap}
  .brand__dot{width:.7em;height:.7em;border-radius:50%;background:var(--blue);display:inline-block}

  /* Letterhead */
  .letterhead{position:absolute;left:430px;top:40px;width:390px;height:552px;background:var(--paper);box-shadow:var(--shadow);padding:34px 36px 28px;display:flex;flex-direction:column}
  .letterhead .brand{font-size:17px;align-self:flex-end;margin-bottom:22px}
  .letterhead__body{font-family:"Arimo",Arial,sans-serif;font-size:7.4px;line-height:1.55;color:#333}
  .letterhead__body p{margin-bottom:9px}
  .letterhead__sign{margin-top:auto;align-self:flex-end;text-align:center;font-family:"Arimo",Arial,sans-serif;font-size:7.5px;letter-spacing:.5px;color:var(--ink-soft)}
  .letterhead__sign-line{width:120px;border-top:1px solid #999;margin:0 auto 4px}
  .letterhead__footer{margin-top:18px;font-size:6.4px;line-height:1.6;color:var(--ink)}
  .letterhead__footer strong{color:var(--blue);font-weight:700}
  .letterhead__footer .label{color:var(--blue)}

  /* Folder */
  .folder{position:absolute;left:860px;top:70px;width:300px;height:424px;background:linear-gradient(160deg,#28a4df 0%,#1586cf 55%,var(--blue-deep) 100%);box-shadow:var(--shadow)}

  /* Envelope */
  .envelope{position:absolute;left:440px;top:628px;width:470px;height:232px;background:var(--paper);box-shadow:var(--shadow);display:flex;flex-direction:column}
  .envelope__face{flex:1;display:flex;align-items:center;justify-content:center}
  .envelope .brand{font-size:24px}
  .envelope__band{height:46px;background:var(--blue)}

  /* Business cards */
  .card{position:absolute;width:340px;height:196px;box-shadow:var(--shadow)}
  .card--front{left:40px;top:300px;background:var(--paper);padding:16px 20px 12px;display:flex;flex-direction:column;align-items:center}
  .card--front .brand{font-size:12px}
  .card__name{margin-top:12px;font-size:14px;font-weight:700;color:var(--blue)}
  .card__title{font-size:8px;color:var(--ink-soft);margin-bottom:10px}
  .card__contacts{align-self:stretch;font-size:6.6px;line-height:1.65;color:var(--ink)}
  .card__contacts .label{color:var(--blue);font-weight:600}
  .card__slogan{margin-top:auto;font-size:7.5px;letter-spacing:.8px;color:var(--ink-soft);font-weight:600}

  .card--back{left:40px;top:530px;background:linear-gradient(180deg,var(--blue) 0%,#1a7fcc 100%);color:#fff;padding:16px 20px 14px;display:flex;flex-direction:column}
  .card__heading{font-size:9px;font-weight:700;text-align:center;margin-bottom:6px}
  .card__services{list-style:none;display:grid;grid-template-columns:1fr 1fr;gap:2px 12px;font-size:7px;line-height:1.45}
  .card__services li::before{content:"• "}
  .card--back .card__slogan{color:#fff;text-align:center;font-size:8.5px;font-weight:700}
</style>
</head>
<body>

<section class="letterhead" aria-label="Letterhead">
  <div class="brand"><span class="brand__dot"></span>Harrowmere Freight</div>
  <div class="letterhead__body">
    <p>Lorem Ipsum is simply dummy text of the printing and typesetting industry. Lorem Ipsum has been the industry's standard dummy text ever since the 1500s, when an unknown printer took a galley of type and scrambled it to make a type specimen book. It has survived not only five centuries, but also the leap into electronic typesetting, remaining essentially unchanged. It was popularised in the 1960s with the release of Letraset sheets containing Lorem Ipsum passages, and more recently with desktop publishing software like Aldus PageMaker including versions of Lorem Ipsum.</p>
    <p>Established fact that a reader will be distracted by the readable content of a page when looking at its layout. The point of using Lorem Ipsum is that it has a more-or-less normal distribution of letters, as opposed to using 'Content here, content here', making it look like readable English.</p>
    <p>Many desktop publishing packages and web page editors now use Lorem Ipsum as their default model text, and a search for 'lorem ipsum' will uncover many web sites still in their infancy. Various versions have evolved over the years, sometimes by accident, sometimes on purpose (injected humour and the like).</p>
    <p>Established fact that a reader will be distracted by the readable content of a page when looking at its layout. The point of using Lorem Ipsum is that it has a more-or-less normal distribution of letters, as opposed to using 'Content here, content here', making it look like readable English.</p>
  </div>
  <div class="letterhead__sign">
    <div class="letterhead__sign-line"></div>
    DANIEL LIM
  </div>
  <div class="letterhead__footer">
    <strong>HARROWMERE FREIGHT SDN BHD (1204387-K)</strong><br>
    <span class="label">Address:</span> No. 8, 2nd Floor, Jalan Kenari 5, Bandar Puchong Jaya, 47100 Puchong, Selangor, Malaysia.<br>
    <span class="label">Tel:</span> (603) 2718 4406 • <span class="label">Fax:</span> (603) 2718 4410 • <span class="label">Email:</span> enquiry@harrowmere.com.my<br>
    <span class="label">GST Registration No:</span> 001845720193
  </div>
</section>

<section class="folder" aria-label="Presentation folder"></section>

<section class="envelope" aria-label="Envelope">
  <div class="envelope__face"><div class="brand"><span class="brand__dot"></span>Harrowmere Freight</div></div>
  <div class="envelope__band"></div>
</section>

<section class="card card--front" aria-label="Business card front">
  <div class="brand"><span class="brand__dot"></span>Harrowmere Freight</div>
  <div class="card__name">Farid Hassan</div>
  <div class="card__title">Managing Director</div>
  <div class="card__contacts">
    <span class="label">Office:</span> No. 8, Jalan Kenari 5, 47100 Puchong, Selangor, Malaysia<br>
    <span class="label">Tel:</span> (603) 2718 4406 &nbsp; <span class="label">Cell:</span> (6012) 384 7751 &nbsp; <span class="label">Fax:</span> (603) 2718 4410<br>
    <span class="label">Email:</span> farid@harrowmere.com.my &nbsp; <span class="label">Web:</span> www.harrowmere.com.my
  </div>
  <div class="card__slogan">ONE STOP LOGISTICS SOLUTIONS</div>
</section>

<section class="card card--back" aria-label="Business card back">
  <div class="card__heading">We're Specialise In</div>
  <ul class="card__services">
    <li>International Shipping (Air/Sea)</li>
    <li>Supply Chain Management</li>
    <li>Tax Exemption Consultancy</li>
    <li>Packing</li>
    <li>Consolidation • NVOCC</li>
    <li>Project Transportation</li>
    <li>Warehousing • Distribution</li>
    <li>Custom Brokerage</li>
    <li>Marine Insurance</li>
    <li>Door to Door</li>
  </ul>
  <div class="card__slogan">ONE STOP LOGISTICS SOLUTIONS</div>
</section>

</body>
</html>
```